Keystonery Billboard - Financial Services Company (Investments, Tax Planning and Insurance)

Our new office has a billboard directly above the office building. We'd like something eye-catching with a strong Call to Action, with the main part of the billboard being under 7 words if possible. We'd like you to include a way to get ahold of us (either our website keystoneryllc.example or our phone number 302-418-2907. You may also include in small font something to indicate that we've been serving the area since 1980 (the DE area, the tri-state area, the Marlowe Hollow, etc.)

We offer financial planning, tax planning, and insurance, and we help our clients to focus on their goals and happiness by providing everything they need for lifelong wealth under one roof.

Our logos are attached, we use a triangle logo with green and gray. We use the tagline "discover lasting prosperity" but this does not need to be included.

Potential ideas we have seen from other financial companies-
- the concept that the driver spends more time looking at billboards than planning for their retirement
-something along the lines of "everything you need for your finances is in this building right here" planning, investments, taxes, insurance"
-don't spend your time worrying about retirement, let us help you plan for it
-are you working for your money, or is it working for you?
- retirement takes planning, we're here to help
- ready to retire? talk to us
- need investment advice?
- need help investing?
- crossing your fingers isn't a retirement plan. we can help.
- retiring soon? you need help.

Those are just general ideas, please feel free to be creative.

brand colors:
#00b585
#00b185
#000000
#ffffff
#6d6f75
#6d6f75
#6f7074
#021712
#052e24

```html
<!DOCTYPE html>
<html lang="en">
<head>
<meta charset="utf-8">
<title>Keystonery Billboard</title>
<link rel="stylesheet" href="https://fonts.googleapis.com/css2?family=Poppins:wght@400;500;600;700;800&display=swap">
<style>
  :root {
    --page-bg: #dedede;
    --paper: #ffffff;
    --brand-green: #00985f;
    --brand-green-dark: #008552;
    --ink: #3d3d40;
    --ink-soft: #6d6f75;
    --tag-gray: #46474b;
    --photo-top: #8c8c8c;
    --photo-mid: #6f6458;
    --photo-bottom: #4a3a2a;
  }
  html, body {
    margin: 0;
    width: 896px;
    height: 1200px;
    overflow: hidden;
    background: var(--page-bg);
  }
  .billboard {
    position: absolute;
    left: 24px;
    top: 462px;
    width: 848px;
    height: 275px;
    display: block;
    filter: drop-shadow(10px 12px 8px rgba(0,0,0,0.28));
    font-family: "Poppins", sans-serif;
  }
  .brand-name { font-weight: 600; fill: var(--brand-green); }
  .brand-tagline { font-weight: 400; fill: var(--ink-soft); letter-spacing: 4px; }
  .headline { font-weight: 700; fill: var(--ink); }
  .service-label { font-weight: 600; fill: var(--paper); }
  .web-dark { fill: var(--ink); }
  .web-green { fill: var(--brand-green); }
  .web-address { font-weight: 700; }
  .since-note { font-weight: 600; fill: var(--paper); }
  .icon-ring { fill: none; stroke: var(--paper); stroke-width: 2.5; }
  .icon-glyph { fill: var(--paper); }
  .service-divider { stroke: var(--brand-green-dark); stroke-width: 2; }
</style>
</head>
<body>
<svg class="billboard" viewBox="0 0 1465 475" xmlns="http://www.w3.org/2000/svg">
  <defs>
    <linearGradient id="photoTone" x1="0" y1="0" x2="0" y2="1">
      <stop offset="0" stop-color="var(--photo-top)"/>
      <stop offset="0.55" stop-color="var(--photo-mid)"/>
      <stop offset="1" stop-color="var(--photo-bottom)"/>
    </linearGradient>
  </defs>

  <rect class="board-paper" x="0" y="0" width="1465" height="475" fill="var(--paper)"/>

  <polygon class="board-photo" points="1232,0 1465,0 1465,475 963,475" fill="url(#photoTone)" role="img" aria-label="Photo of young plants growing from stacks of gold coins in soil"/>

  <!-- brand -->
  <text class="brand-name" x="60" y="100" font-size="66">Keystonery</text>
  <text class="brand-tagline" x="63" y="124" font-size="12">DISCOVER LASTING PROSPERITY</text>

  <!-- headline -->
  <text class="headline" x="58" y="212" font-size="96" textLength="1032" lengthAdjust="spacingAndGlyphs">NEED HELP INVESTING?</text>

  <!-- services band -->
  <polygon class="service-band" points="0,240 1082,240 998,388 0,388" fill="var(--brand-green)"/>
  <line class="service-divider" x1="265" y1="262" x2="265" y2="366"/>
  <line class="service-divider" x1="493" y1="262" x2="493" y2="366"/>
  <line class="service-divider" x1="775" y1="262" x2="775" y2="366"/>

  <g class="service service-financial">
    <circle class="icon-ring" cx="82" cy="313" r="23"/>
    <rect class="icon-glyph" x="69" y="300" width="16" height="5" rx="2"/>
    <rect class="icon-glyph" x="69" y="307" width="16" height="5" rx="2"/>
    <rect class="icon-glyph" x="69" y="314" width="16" height="5" rx="2"/>
    <circle class="icon-glyph" cx="92" cy="318" r="8"/>
    <text x="88.5" y="322" font-size="11" font-weight="700" fill="var(--brand-green)" font-family="Poppins, sans-serif">$</text>
    <text class="service-label" x="114" y="308" font-size="24">FINANCIAL</text>
    <text class="service-label" x="114" y="333" font-size="24">PLANNING</text>
  </g>

  <g class="service service-tax">
    <circle class="icon-ring" cx="314" cy="313" r="23"/>
    <rect class="icon-glyph" x="303" y="299" width="22" height="26" rx="2"/>
    <rect x="306" y="309" width="16" height="7" fill="var(--brand-green)"/>
    <text x="307" y="315" font-size="6" font-weight="700" fill="var(--paper)" font-family="Poppins, sans-serif">TAX</text>
    <text class="service-label" x="346" y="308" font-size="24">TAX</text>
    <text class="service-label" x="346" y="333" font-size="24">PLANNING</text>
  </g>

  <g class="service service-investment">
    <circle class="icon-ring" cx="543" cy="313" r="23"/>
    <rect class="icon-glyph" x="532" y="313" width="5" height="11"/>
    <rect class="icon-glyph" x="540" y="307" width="5" height="17"/>
    <rect class="icon-glyph" x="548" y="301" width="5" height="23"/>
    <text class="service-label" x="575" y="308" font-size="24">INVESTMENT</text>
    <text class="service-label" x="575" y="333" font-size="24">MANAGEMENT</text>
  </g>

  <g class="service service-insurance">
    <circle class="icon-ring" cx="823" cy="313" r="23"/>
    <path class="icon-glyph" d="M809,313 A14,13 0 0 1 837,313 Z"/>
    <path d="M823,313 L823,322 A3,3 0 0 1 817,322" fill="none" stroke="var(--paper)" stroke-width="2.5"/>
    <text class="service-label" x="855" y="322" font-size="24">INSURANCE</text>
  </g>

  <!-- contact row -->
  <text class="web-address" x="55" y="446" font-size="40" textLength="510" lengthAdjust="spacingAndGlyphs"><tspan class="web-dark">www.</tspan><tspan class="web-green">keystoneryllc</tspan><tspan class="web-dark">.example</tspan></text>

  <polygon class="since-tag" points="622,398 990,398 948,475 578,475" fill="var(--tag-gray)"/>
  <text class="since-note" x="785" y="443" font-size="20" text-anchor="middle">SERVING THIS AREA SINCE 1980</text>
</svg>
</body>
</html>
```